Specialised investor in e-mobility and energy wants business card design

We need a business card design that fits our existing corporate design. <The look and feel must be 'sharp'/'clean', dynamic, communicate momentum, professionalism etc (as one would imagine from a firm in the financial sector). We like the idea of a reverse-side of the card that includes the logo, and the name and contact details on the other. We expect the deliverable to be whatever format might be required to be able to get cards printed directly by a service such as kelmo press. Our website is www.zub.capital

```html
<!DOCTYPE html>
<html lang="en">
<head>
<meta charset="utf-8">
<title>Zub Capital business card</title>
<link href="https://fonts.googleapis.com/css2?family=Montserrat:wght@400;500;700;800&display=swap" rel="stylesheet">
<style>
  :root {
    --green-dark: #345226;
    --green-light: #7ab648;
    --paper: #ffffff;
    --backdrop: #2b2e33;
    --icon-bg: #8cc152;
  }
  * { margin: 0; padding: 0; box-sizing: border-box; }
  html, body { width: 1200px; height: 952px; overflow: hidden; }
  body {
    background: var(--backdrop);
    font-family: "Montserrat", sans-serif;
    position: relative;
  }
  .card {
    position: absolute;
    left: 220px;
    width: 760px;
    height: 434px;
    background: var(--paper);
    overflow: hidden;
    box-shadow: 0 6px 18px rgba(0,0,0,.35);
  }
  .card--back { top: 30px; }
  .card--front { top: 488px; }

  .brand {
    position: absolute;
    display: flex;
    align-items: center;
    gap: 14px;
    color: var(--green-dark);
    font-weight: 500;
    white-space: nowrap;
  }
  .brand__mark { background: var(--green-dark); flex: none; }
  .card--back .brand { left: 210px; top: 140px; font-size: 62px; }
  .card--back .brand__mark { width: 26px; height: 26px; }
  .card--front .brand { left: 128px; top: 60px; font-size: 40px; }
  .card--front .brand__mark { width: 18px; height: 18px; }

  .web-band {
    position: absolute;
    left: 0; right: 0;
    top: 292px;
    height: 36px;
    background: var(--green-dark);
    color: var(--paper);
    font-size: 15px;
    letter-spacing: 5px;
    line-height: 36px;
    padding-left: 190px;
  }

  .contact-band {
    position: absolute;
    left: 0; top: 170px;
    width: 400px; height: 150px;
  }
  .contact-band__shape { position: absolute; inset: 0; }
  .contact-list {
    position: absolute;
    left: 44px; top: 24px;
    list-style: none;
    color: var(--paper);
    font-size: 17px;
    font-weight: 500;
  }
  .contact-list li { display: flex; align-items: center; gap: 12px; height: 34px; }
  .contact-icon {
    width: 22px; height: 22px; border-radius: 4px;
    background: var(--icon-bg);
    display: flex; align-items: center; justify-content: center;
    flex: none;
  }
  .contact-icon svg { display: block; }

  .person {
    position: absolute;
    right: 70px; top: 232px;
    text-align: right;
  }
  .person__name {
    color: var(--green-dark);
    font-size: 32px;
    font-weight: 800;
    letter-spacing: 1px;
  }
  .person__role {
    color: var(--green-light);
    font-size: 19px;
    font-weight: 500;
    letter-spacing: 1px;
  }
</style>
</head>
<body>

  <section class="card card--back">
    <div class="brand"><span class="brand__mark"></span>Zub Capital</div>
    <div class="web-band">www.zub.capital</div>
  </section>

  <section class="card card--front">
    <div class="brand"><span class="brand__mark"></span>Zub Capital</div>

    <div class="contact-band">
      <svg class="contact-band__shape" width="400" height="150" viewBox="0 0 400 150">
        <path d="M0 0 H400 L330 150 H0 Z" fill="#345226"/>
      </svg>
      <ul class="contact-list">
        <li>
          <span class="contact-icon">
            <svg width="14" height="14" viewBox="0 0 24 24"><path d="M6.6 10.8a15 15 0 0 0 6.6 6.6l2.2-2.2a1 1 0 0 1 1-.25 11.4 11.4 0 0 0 3.6.6 1 1 0 0 1 1 1V20a1 1 0 0 1-1 1A17 17 0 0 1 3 4a1 1 0 0 1 1-1h3.5a1 1 0 0 1 1 1c0 1.25.2 2.45.6 3.6a1 1 0 0 1-.25 1z" fill="#fff"/></svg>
          </span>+41 79555 0142
        </li>
        <li>
          <span class="contact-icon">
            <svg width="14" height="14" viewBox="0 0 24 24"><rect x="2" y="5" width="20" height="14" fill="none" stroke="#fff" stroke-width="2"/><path d="M2 5l10 8 10-8" fill="none" stroke="#fff" stroke-width="2"/></svg>
          </span>jana@zub.capital
        </li>
        <li>
          <span class="contact-icon">
            <svg width="14" height="14" viewBox="0 0 24 24"><path d="M12 2a7 7 0 0 0-7 7c0 5 7 13 7 13s7-8 7-13a7 7 0 0 0-7-7zm0 9.5A2.5 2.5 0 1 1 12 6.5a2.5 2.5 0 0 1 0 5z" fill="#fff"/></svg>
          </span>Geneva, Switzerland
        </li>
      </ul>
    </div>

    <div class="person">
      <div class="person__name">JANA MOOR</div>
      <div class="person__role">Manager</div>
    </div>
  </section>

</body>
</html>
```